Drone service provider needs a brilliant web design

I need a responsive web design for a new drone service company. Pelham Drone Solutions provides turnkey solutions to capture, process, and deliver actionable aerial data to customers. The design should communicate a professional company that is safe, legal and insured. I included our logo design and business card designs for reference.
*content to be supplied after design selected

Target Market(s)

We serve telecommunications, construction, government, utility infrastructure, insurance and other industries.

Industry/Entity Type

Industrial

Number of Pages Required

5+ page

Colors

Designer to choose colors to be used in the design.

Requirements
Must have
• The design should highlight professional services to include Inspections, Mapping, Consulting and Training. The site should include aerial images and video to compliment the services offered. The landing page must include following sections in order: HOME, SERVICES, ABOUT, DEMO REEL, CLIENTS, CONTACT FORM, and social media buttons (Facebook, LinkedIn, Twitter, YouTube, Instagram). Contact: 615-382-9041 info@pelhamdronesolutions-example.com Smyrna, TN
• Sitemap:
• 6 pages: Home, Inspections, Mapping, Training, Consulting, About
• HOME (Landing Page)
• • Header with logo and tab links (Home, Services, About, Contact)
• • 'CAPTURE. PROCESS. DELIVER.' tagline and 'CONTACT US' button displayed within aerial image of drone over city or construction site
• • Services section with icons, text and read more link to page
• • About section with photo and text with three icons for SAFE. LEGAL. INSURED.
• • Demo reel
• • Clients logos shown scrolling horizontally
• • Contact form
• • Footer with logo, phone, email, social media buttons
• SERVICES (4 different pages)
• • Inspections
• • Mapping
• • Consulting
• • Training
• ABOUT page
• • Company
• • Partners
• • Certifications & Associations
• • Careers
• CONTACT linked to bottom of landing page
• Would you like to receive the newsletter? Yes or No Drop-down list
Nice to have
• Photos of KVR Marlin or Corvex inspecting infrastructure, buildings, construction sites, etc. A photo of one or two pilots in vest and helmet. Free stock photos preferred but would purchase the right photo that's more relevant.
• website references:
• https://www.quillrotor-example.com/
• https://www.brentfieldworks-example.com/services
• https://www.tomaro-example.com/
• http://gantrymetric-example.com/
• http://lumbrook-example.com/
• http://fennotics-example.com/
• https://www.grebe-example.io/
Should not have
• not an aerial photography or videography service business, no blog or newsletter

```html
<!DOCTYPE html>
<html lang="en">
<head>
<meta charset="utf-8">
<title>Pelham Drone Solutions</title>
<link rel="stylesheet" href="https://fonts.googleapis.com/css2?family=Poppins:wght@300;400;500;600;700&display=swap">
<style>
:root{
  --blue:#0a86d8;
  --ink:#1d1d1d;
  --text:#444;
  --paper:#ffffff;
  --mist:#f0f0f0;
  --night:#141414;
  --white:#ffffff;
}
*{box-sizing:border-box;margin:0;padding:0}
html,body{width:1200px;height:3475px;overflow:hidden}
body{font-family:"Poppins",sans-serif;color:var(--ink);background:var(--paper)}
.page{position:relative;width:1200px;height:3475px;overflow:hidden;background:var(--paper)}
.abs{position:absolute}
.backdrop{position:absolute;left:0;top:0}
.header{position:absolute;left:0;top:0;width:1200px;height:81px;background:var(--white);z-index:3}
.brand{position:absolute;left:160px;top:28px;font-weight:700;font-size:19px;color:var(--ink);display:flex;align-items:center;gap:9px;white-space:nowrap}
.brand-dot{width:12px;height:12px;border-radius:50%;background:var(--blue)}
.nav{position:absolute;top:33px;left:519px;font-size:14px}
.nav a{position:absolute;color:var(--ink);text-decoration:none;white-space:nowrap}
.nav a.active{color:var(--blue)}
.login{position:absolute;left:962px;top:27px;width:74px;height:34px;border-radius:17px;background:var(--blue);color:var(--white);font-size:12px;font-weight:600;display:flex;align-items:center;justify-content:center}
.hero-title{position:absolute;top:240px;left:0;width:1200px;text-align:center;color:var(--white);font-size:50px;font-weight:500}
.tagline{position:absolute;top:305px;left:0;width:1200px;display:flex;justify-content:center;align-items:center;gap:26px;color:var(--white);font-size:28px;font-weight:500}
.tag-dot{width:18px;height:18px;border-radius:50%;background:var(--blue);border:3px solid var(--white)}
.btn-ghost{position:absolute;left:538px;top:359px;width:125px;height:42px;border:2px solid var(--white);border-radius:21px;color:var(--white);font-size:12px;font-weight:600;display:flex;align-items:center;justify-content:center}
.slider-dots{position:absolute;left:512px;top:510px;display:flex;gap:6px}
.slider-dots span{width:40px;height:4px;background:rgba(255,255,255,.75)}
.section-title{position:absolute;left:0;width:1200px;text-align:center;font-size:34px;font-weight:500}
.section-lede{position:absolute;text-align:center;font-size:12px;line-height:26px}
.about-title{position:absolute;left:160px;top:678px;font-size:27px;font-weight:500}
.about-copy{position:absolute;left:160px;top:738px;width:462px;font-size:11px;line-height:23.5px;color:var(--text)}
.btn-solid{position:absolute;display:flex;align-items:center;justify-content:center;border-radius:22px;color:var(--white);font-size:12px;font-weight:600}
.drone-photo{position:absolute;left:660px;top:705px;width:450px;height:220px;border-radius:6px;background:radial-gradient(ellipse at center,#6a6d73 0%,#c9cbcf 45%,rgba(255,255,255,0) 72%)}
.service{position:absolute;top:1277px;width:220px;text-align:center;color:var(--white)}
.service-icon{width:94px;height:94px;border-radius:50%;background:var(--white);margin:0 auto;display:flex;align-items:center;justify-content:center;border:4px solid var(--blue);box-shadow:0 0 0 3px var(--white)}
.service h3{font-size:16px;font-weight:400;margin-top:13px}
.service p{font-size:10.5px;line-height:19px;margin:10px auto 0;width:160px}
.video{position:absolute;left:215px;top:1807px;width:770px;height:336px;background:linear-gradient(160deg,#8e7a5c 0%,#4d4c46 40%,#2c3137 75%,#3e4750 100%)}
.play{position:absolute;left:558px;top:1932px;width:84px;height:84px;border-radius:50%;border:4px solid var(--white);background:rgba(0,0,0,.35);display:flex;align-items:center;justify-content:center}
.gallery-item{position:absolute;top:2382px;width:281px;height:255px}
.arrow{position:absolute;top:2487px;width:44px;height:44px;border-radius:50%;background:var(--white);border:1px solid #bbb;display:flex;align-items:center;justify-content:center}
.contact-text{position:absolute;left:300px;top:2896px;width:600px;text-align:center;color:var(--white);font-size:12.5px;line-height:28px}
.field{position:absolute;background:var(--white);font-size:11px;color:#555;padding:8px 6px}
.footer-brand{position:absolute;left:160px;top:3252px;color:var(--white);font-weight:700;font-size:16px;display:flex;align-items:center;gap:8px;white-space:nowrap}
.footer-about{position:absolute;left:160px;top:3310px;width:260px;font-size:11.5px;line-height:19px;color:#ddd}
.footer-col{position:absolute;top:3244px;color:var(--white)}
.footer-col h4{font-size:15px;font-weight:400;margin-bottom:14px}
.footer-col li{list-style:none;font-size:11.5px;line-height:19.5px;color:#ddd}
.contact-line{display:flex;gap:10px;font-size:11.5px;line-height:19px;color:#ddd;margin-bottom:12px;white-space:nowrap}
.contact-line b{color:var(--blue);font-weight:400}
.footer-rule{position:absolute;left:160px;top:3406px;width:880px;height:1px;background:#444}
.social{position:absolute;left:160px;top:3432px;display:flex;align-items:center;gap:14px;color:var(--white);font-size:15px;font-weight:500}
.social-dot{width:13px;height:13px;border-radius:50%;background:var(--white)}
.legal{position:absolute;left:627px;top:3436px;font-size:11px;color:#ddd}
</style>
</head>
<body>
<div class="page">

  <svg class="backdrop" width="1200" height="3475" viewBox="0 0 1200 3475" aria-hidden="true">
    <polygon points="0,2247 1200,2016 1200,2699 0,2838" fill="var(--mist)"/>
    <polygon points="0,1089 1200,915 1200,1541 0,1715" fill="var(--blue)"/>
    <polygon points="0,2838 1200,2699 1200,3209 0,3209" fill="var(--blue)"/>
    <rect x="0" y="3209" width="1200" height="266" fill="var(--night)"/>
  </svg>

  <div class="abs" role="img" aria-label="Aerial photograph of city highway interchanges at dusk"
       style="left:0;top:81px;width:1200px;height:568px;background:linear-gradient(135deg,#2b3038,#5a6068 45%,#3a3f46 75%,#23272d);clip-path:polygon(0 0,100% 0,100% 67.6%,0 100%)"></div>

  <header class="header">
    <div class="brand"><span class="brand-dot"></span>Pelham Drone Solutions</div>
    <nav class="nav">
      <a class="active" style="left:0">Home</a>
      <a style="left:67px">Services</a>
      <a style="left:146px">Blog</a>
      <a style="left:201px">Videos</a>
      <a style="left:269px">About us</a>
      <a style="left:354px">Contact us</a>
    </nav>
    <div class="login">LOGIN</div>
  </header>

  <h1 class="hero-title">Pelham Drone Solutions</h1>
  <div class="tagline"><span>Capture</span><span class="tag-dot"></span><span>Process</span><span class="tag-dot"></span><span>Deliver</span></div>
  <div class="btn-ghost">READ MORE</div>
  <div class="slider-dots"><span></span><span></span><span></span><span></span></div>

  <h2 class="about-title">About Pelham Drone Solutions</h2>
  <p class="about-copy">Sed ut perspiciatis unde omnis iste natus error sit voluptatem accusantium doloremque laudantium, totam rem aperiam, eaque ipsa quae ab illo inventore veritatis et quasi architecto beatae vitae dicta sunt explicabo. Nemo enim ipsam voluptatem quia voluptas sit aspernatur aut odit aut fugit, sed quia consequuntur magni dolores eos qui ratione voluptatem sequi nesciunt. Neque porro quisquam est, qui dolorem ipsum quia dolor sit amet, consectetur, adipisci velit, sed quia non numquam eius modi tempora incidunt ut labore et dolore magnam aliquam quaerat voluptatem, sed quia consequuntur magni dolores.</p>
  <div class="btn-solid" style="left:160px;top:971px;width:113px;height:39px;background:var(--blue)">READ MORE</div>
  <div class="drone-photo" role="img" aria-label="Photo of a multi-rotor drone carrying a camera gimbal"></div>

  <h2 class="section-title" style="top:1145px;color:var(--white)">Services</h2>
  <p class="section-lede" style="top:1198px;left:290px;width:620px;color:var(--white)">Sed ut perspiciatis unde omnis iste natus error sit voluptatem accusantium doloremque laudantium, totam rem aperiam, eaque ipsa quae ab illo inventore ver</p>

  <div class="service" style="left:143px">
    <div class="service-icon"><svg width="46" height="46" viewBox="0 0 46 46" fill="none" stroke="var(--blue)" stroke-width="2.5"><rect x="6" y="8" width="26" height="32" rx="2"/><rect x="13" y="4" width="12" height="7" rx="2"/><circle cx="27" cy="27" r="7"/><line x1="32" y1="32" x2="40" y2="40"/></svg></div>
    <h3>Inspections</h3>
    <p>Sed ut perspiciatis unde othe voluptatem accusan tium dolore mq ue laudptia te iu doori</p>
  </div>
  <div class="service" style="left:374px">
    <div class="service-icon"><svg width="46" height="46" viewBox="0 0 46 46" fill="none" stroke="var(--blue)" stroke-width="2.5" stroke-linejoin="round"><polygon points="5,9 17,5 29,9 41,5 41,37 29,41 17,37 5,41"/><line x1="17" y1="5" x2="17" y2="37"/><line x1="29" y1="9" x2="29" y2="41"/></svg></div>
    <h3>Mapping</h3>
    <p>Sed ut perspiciatis unde othe voluptatem accusan tium dolore mq ue laudptia te iu doori</p>
  </div>
  <div class="service" style="left:606px">
    <div class="service-icon"><svg width="46" height="46" viewBox="0 0 46 46" fill="none" stroke="var(--blue)" stroke-width="2.5"><circle cx="16" cy="18" r="6"/><path d="M5 40c0-8 5-12 11-12s11 4 11 12"/><rect x="25" y="5" width="17" height="12" rx="2"/><path d="M29 17l-2 5 6-5"/></svg></div>
    <h3>Consulting</h3>
    <p>Sed ut perspiciatis unde othe voluptatem accusan tium dolore mq ue laudptia te iu doori</p>
  </div>
  <div class="service" style="left:838px">
    <div class="service-icon"><svg width="46" height="46" viewBox="0 0 46 46" fill="none" stroke="var(--blue)" stroke-width="2.5"><rect x="16" y="5" width="26" height="18"/><circle cx="9" cy="16" r="4"/><path d="M4 41V26h10v15"/><line x1="14" y1="27" x2="22" y2="20"/><line x1="29" y1="23" x2="29" y2="41"/></svg></div>
    <h3>Training</h3>
    <p>Sed ut perspiciatis unde othe voluptatem accusan tium dolore mq ue laudptia te iu doori</p>
  </div>

  <h2 class="section-title" style="top:1677px">Our Video</h2>
  <p class="section-lede" style="top:1728px;left:200px;width:800px;color:var(--text)">Sed ut perspiciatis unde omnis iste natus error sit voluptatem accusantium doloremque laudantium, totam rem aperiam, eaque ipsa quae ab illo inventore veritatisSed ut perspiciatis unde omnis iste natus error sit voluptatem accusan.</p>
  <div class="video" role="img" aria-label="Video still of an aerial view over an industrial plant at sunset"></div>
  <div class="play"><svg width="30" height="34" viewBox="0 0 30 34"><polygon points="6,3 27,17 6,31" fill="var(--white)"/></svg></div>

  <h2 class="section-title" style="top:2245px">Aerial Gallery</h2>
  <p class="section-lede" style="top:2298px;left:200px;width:800px;color:var(--text)">Sed ut perspiciatis unde omnis iste natus error sit voluptatem accusantium doloremque laudantium, totam rem aperiam, eaque ipsa quae ab illo inventore veritatisSed ut perspiciatis unde omnis iste natus error sit voluptatem accusan.</p>
  <div class="gallery-item" style="left:162px;background:linear-gradient(160deg,#9c8a6c,#4f5153 55%,#2f3438)" role="img" aria-label="Aerial photo of an industrial facility"></div>
  <div class="gallery-item" style="left:461px;background:linear-gradient(150deg,#8d5a47,#6b6f5f 50%,#3e4a3c)" role="img" aria-label="Aerial photo of suburban rooftops"></div>
  <div class="gallery-item" style="left:758px;background:linear-gradient(150deg,#4a3a2e,#7a6a5a 50%,#2c2520)" role="img" aria-label="Aerial photo looking down on city towers"></div>
  <div class="arrow" style="left:103px"><svg width="14" height="14" viewBox="0 0 14 14" fill="none" stroke="#777" stroke-width="2"><polyline points="9,2 4,7 9,12"/></svg></div>
  <div class="arrow" style="left:1055px"><svg width="14" height="14" viewBox="0 0 14 14" fill="none" stroke="#777" stroke-width="2"><polyline points="5,2 10,7 5,12"/></svg></div>

  <h2 class="section-title" style="top:2840px;color:var(--white)">Contact Us</h2>
  <p class="contact-text">Get in touch with us today to have a coffee with us or get more information about how we can help you succeed with your digital and mobile payments strategy.</p>
  <div class="field" style="left:246px;top:2973px;width:347px;height:32px">Name:</div>
  <div class="field" style="left:246px;top:3012px;width:347px;height:35px">Phone:</div>
  <div class="field" style="left:246px;top:3052px;width:347px;height:35px">Email:</div>
  <div class="field" style="left:605px;top:2973px;width:370px;height:114px">Comments:</div>
  <div class="btn-solid" style="left:540px;top:3112px;width:123px;height:44px;background:var(--night)">SUBMIT</div>

  <div class="footer-brand"><span class="brand-dot"></span>Pelham Drone Solutions</div>
  <p class="footer-about">At vero eos et accusamus et iusto odio dignissimos ducimus qui blanditiis pra esentium voluptatum delenit.</p>
  <div class="footer-col" style="left:447px"><h4>About Us</h4><ul><li>Sed utperspiciatis</li><li>Omniste natus</li><li>Sed utperspiciatis</li><li>Hide omniste natus</li><li>Sed utperspiciatis</li></ul></div>
  <div class="footer-col" style="left:619px"><h4>Links</h4><ul><li>Sed utperspiciatis</li><li>Omniste natus</li><li>Sed utperspiciatis</li><li>Hide omniste natus</li><li>Sed utperspiciatis</li></ul></div>
  <div class="footer-col" style="left:781px">
    <h4>Contact</h4>
    <div class="contact-line"><svg width="12" height="16" viewBox="0 0 12 16"><path d="M6 0a6 6 0 0 1 6 6c0 4-6 10-6 10S0 10 0 6a6 6 0 0 1 6-6z" fill="var(--blue)"/><circle cx="6" cy="6" r="2.2" fill="var(--night)"/></svg><span><b>Address:</b> Pelham Drone Solutions,<br>PO Box 12, Smyrna, TN 37167</span></div>
    <div class="contact-line"><svg width="14" height="12" viewBox="0 0 14 12"><rect x="0" y="1" width="14" height="10" fill="var(--blue)"/><polyline points="0,1 7,7 14,1" fill="none" stroke="var(--night)" stroke-width="1.3"/></svg><span><b>E-mail:</b> info@pelhamdronesolutions-example.com</span></div>
    <div class="contact-line"><svg width="12" height="12" viewBox="0 0 12 12"><path d="M2 0h3l1 3-2 1.5a7 7 0 0 0 3.5 3.5L9 6l3 1v3a2 2 0 0 1-2 2A10 10 0 0 1 0 2a2 2 0 0 1 2-2z" fill="var(--blue)"/></svg><span><b>Phone:</b> 615-382-9041</span></div>
  </div>
  <div class="footer-rule"></div>
  <div class="social">Social Media <span class="social-dot" aria-hidden="true"></span><span class="social-dot" aria-hidden="true"></span><span class="social-dot" aria-hidden="true"></span><span class="social-dot" aria-hidden="true"></span></div>
  <p class="legal">© 2017 Pelham Drone Solutions. Disclaimers | Terms of Use | Privacy Policy</p>
</div>
</body>
</html>
```